TLV Accounting Firm Needs Graphic Art for Our Proven Processes and For Our Core Values

**Looking for redesign of attached Powerpoint content (see below)
***Final graphic should be good for web use

Date: March 10, 2017

From: Colin Ashdown, CPA
Ashdown, Pettifer & Associates, P.C. (TLV)

Background:

TLV is a 20 person Houston based CPA firm, providing tax, accounting, financial and consulting services, to individuals and to entrepreneurs and their businesses. TLV is engaged in a process called KLU (See the book Headway, by Lars Obermeyer) whereby we implement a “system” to operate our company. As part of this system we have defined what we call our “Proven Process”. This is something we will show all prospective clients, and have on our website, that explains what it looks like to work with us. Starting at the beginning of the project to completion.

Project Description:

TLV is looking for graphic artist assistance in designing the following pieces:

1. Graphic depiction of “The TLV Way”, otherwise known as our “Proven Process”. The first attachments labeled TLV will show what we have done ourselves. These will show the general steps we have defined in both a sort of graphic way and a step by step narrative. The second attachment shows you some actual examples other firms have put together, hopefully that will show you what we are asking you to develop for us. Note that we are very open to any suggested clarifications or improvements to what we have done which may include changing phrases or saying something in a different way. Remember we are accountants!

2. We have defined our core values as a company, and we are wanting to develop some posters/placards so we can post them in our conference rooms, break room, etc. Attached are our core values as well as some deeper narratives about what they mean. Also included are many of the “words” we kicked around before arriving at our core values.

3. You will also find an attachment with our logo that should be incorporated, as well. Designs SHOULD INCLUDE, but not be limited to, the colors on our logo. Our end product should reflect a strong sense of our core values.

We would like to have the project in a form that would give us the option to use any/all of the information on our website, posters, brochures, etc.

Thanks in advance for your assistance.

Target Market(s)

Entrepreneurs and their companies with revenue greater than one million; Industries such as real estate, construction, trades and professional services; all in the Greater Houston Texas area

Industry/Entity Type

Accounting

Font styles to use
Serif
Other font styles liked:
• We are okay with Serif but are open.

Requirements
Must have
• Proven Process must be presented in a way that is clear and makes sense.
Nice to have
• Clean lines
• Colors should go with logo (see attached)
Should not have
• Can't think of anything - unless I see it

```html
<!DOCTYPE html>
<html lang="en">
<head>
<meta charset="utf-8">
<title>The TLV Way – Our Proven Process</title>
<link rel="stylesheet" href="https://fonts.googleapis.com/css2?family=Open+Sans:wght@400;700&family=Sorts+Mill+Goudy&display=swap">
<style>
  :root {
    --olive: #4e5a2b;
    --gold: #b8923b;
    --gold-light: #c9a24a;
    --text-grey: #4a4a4a;
    --paper: #ffffff;
  }
  html, body {
    margin: 0;
    padding: 0;
    overflow: hidden;
    background: var(--paper);
  }
  .canvas {
    position: relative;
    width: 1200px;
    height: 927px;
    overflow: hidden;
    background: var(--paper);
  }
  .headline {
    position: absolute;
    left: 71px;
    top: 58px;
    margin: 0;
    font-family: "Open Sans", sans-serif;
    font-weight: 700;
    font-size: 62px;
    letter-spacing: 0.5px;
    color: var(--olive);
    line-height: 1;
  }
  .headline-rule {
    position: absolute;
    left: 73px;
    top: 139px;
    width: 440px;
    height: 2px;
    background: linear-gradient(90deg, var(--gold) 0%, var(--gold) 55%, rgba(184,146,59,0) 100%);
  }
  .subhead {
    position: absolute;
    left: 71px;
    top: 152px;
    margin: 0;
    font-family: "Sorts Mill Goudy", serif;
    font-weight: 400;
    font-size: 55px;
    color: var(--gold);
    line-height: 1.1;
  }
  .staircase {
    position: absolute;
    left: 0;
    top: 0;
    width: 1200px;
    height: 927px;
  }
  .step-label {
    position: absolute;
    margin: 0;
    font-family: "Sorts Mill Goudy", serif;
    font-size: 27px;
    line-height: 36px;
    color: var(--gold);
    white-space: nowrap;
  }
  .step-note {
    position: absolute;
    margin: 0;
    font-family: "Open Sans", sans-serif;
    font-size: 19.5px;
    line-height: 26px;
    color: var(--text-grey);
    white-space: nowrap;
  }
  .step-note .indent { padding-left: 14px; }
  .firm-mark {
    position: absolute;
    left: 895px;
    top: 740px;
    width: 56px;
    height: 56px;
    border: 2px solid var(--gold);
    box-sizing: border-box;
  }
  .firm-name {
    position: absolute;
    left: 700px;
    top: 808px;
    width: 450px;
    margin: 0;
    text-align: center;
    font-family: "Sorts Mill Goudy", serif;
    font-size: 25px;
    color: var(--text-grey);
    white-space: nowrap;
  }
  .footer-band {
    position: absolute;
    left: 0;
    bottom: 0;
    width: 1200px;
    height: 21px;
    background: linear-gradient(90deg, var(--gold-light) 0%, var(--gold) 40%, var(--olive) 100%);
  }
</style>
</head>
<body>
<main class="canvas">
  <h1 class="headline">THE TLV WAY</h1>
  <div class="headline-rule"></div>
  <h2 class="subhead">Our Proven Process</h2>

  <svg class="staircase" viewBox="0 0 792 612" aria-hidden="true">
    <path d="M48 565 V465 H108 V405 H168 V345 H228 V285 H288 V225 H348 V165 H408 V101 H715"
          fill="none" stroke="#b8923b" stroke-width="1.8"/>
  </svg>

  <p class="step-label" style="left:91px; top:723px;">Philosophical<br>match</p>
  <p class="step-note" style="left:277px; top:731px;">• Initial meetivng</p>

  <p class="step-label" style="left:182px; top:630px;">Determine<br>your needs</p>
  <p class="step-note" style="left:335px; top:638px;">• Client onboarding<br><span class="indent">questionnaire</span></p>

  <p class="step-label" style="left:273px; top:539px;">Assign client<br>service staff</p>
  <p class="step-note" style="left:451px; top:547px;">• Personal contact<br><span class="indent">within 48 hours</span></p>

  <p class="step-label" style="left:364px; top:445px;">Deeper dive<br>into your situation</p>
  <p class="step-note" style="left:609px; top:454px;">• Request<br><span class="indent">additional data</span></p>

  <p class="step-label" style="left:455px; top:353px;">Prepare draft<br>delivarable</p>
  <p class="step-note" style="left:633px; top:361px;">• For tax returns, turnaround is<br><span class="indent">generally 10 business days</span></p>

  <p class="step-label" style="left:545px; top:261px;">Execute final<br>deliverable</p>
  <p class="step-note" style="left:724px; top:263px;">• File tax return</p>

  <p class="step-label" style="left:636px; top:170px;">Complete<br>feedback loop</p>
  <p class="step-note" style="left:824px; top:167px;">• Were your expectations met?<br><span class="indent">How can we improve?</span></p>

  <div class="firm-mark"></div>
  <p class="firm-name">Ashdown, Pettifer &amp; Associates, PC</p>

  <div class="footer-band"></div>
</main>
</body>
</html>
```